Online Shop Maren

We need a web design for an online shop, called "Lirvo Dune Jewels". The shop should have an extraordinary, elegant look, as shown in the Quellwick Advertising Picture in our Briefing.pdf (attached). Please have a look at our Briefing regarding website colours, background ideas, and elements to be included. The online shop is about professional jewellery design pieces, where each piece is handmade of high quality materials, also unique pieces and unique editions possible. It should attract extraordinary people and visualize that its a very individual and unique design jewellery. You can get an idea of whom it should attract by reading our target group. Colours to be used are jewellery-Velvet red, Black / anthracite, exclusive colours, silverish-white, bronze-brown and golden.

Please play around when designing with the image pictures we attach, preferably more vertical pictures, no panoramic pictures like in Brovenka Shop. Also include the BLACK logo of lirvo dune. We include the SITEMAP in the briefing and also another folder with product pictures you can use for the draft.

Regarding Functions, the store will have the SAME (technical) functions as this page:http://www.brovenka-shop.eu/ - using the "most famous" products/categories for the starting page, going into individual product pages by clicking these images and then leading to a detailed page for one product only.

Target Market(s)

Jewellery-lovers, who appreciate extraordinary things, creative economy/fashion-industries, stylists, Style consultants, outfitter, theatres, operas, production sites, Cocktail-, Dinner and Bridefashion, exclusive traditional costume stores, dancesports and tango argento dancers

Industry/Entity Type

Shop

Requirements
Must have
• Must include:
• Colours as per briefing
• Background ideas/images as per briefing/pictures sent
• Sitemap as per briefing
• Social buttons
• Logo
• Design for 3 pages: Starting page showing big images, attractive design and the 4 popular categories
• Subpage with different products of one category (i.e. bracelets)
• Detail page with one individual product only
Should not have
• no fresh, playful colours like yellow, orange, green, blue
• no cheap design, no panorama pictures

```html
<!DOCTYPE html>
<html lang="en">
<head>
<meta charset="utf-8">
<title>Lirvo Dune Jewels</title>
<link href="https://fonts.googleapis.com/css2?family=Open+Sans:wght@300;400;600;700&display=swap" rel="stylesheet">
<style>
:root{
  --red:#c8161d;
  --red-dark:#a51117;
  --ink:#1e1e1e;
  --topbar:#1c1c1c;
  --hero:#272727;
  --paper:#efefef;
  --card:#ffffff;
  --footer:#1b1b1b;
  --field:#2b2b2b;
  --muted:#8a8a8a;
  --line:#3a3a3a;
}
*{margin:0;padding:0;box-sizing:border-box}
html,body{width:667px;height:1200px;overflow:hidden}
body{font-family:'Open Sans',Arial,sans-serif;color:var(--ink);background:var(--paper);position:relative}
.abs{position:absolute}

/* top bar */
.topbar{left:0;top:0;width:667px;height:27px;background:var(--topbar);color:#fff}
.support{left:62px;top:5px;display:flex;gap:6px;align-items:center}
.support strong{display:block;font-size:7px;font-weight:600;line-height:9px}
.support span{display:block;font-size:5.5px;color:#aaa;line-height:7px}
.toplinks{left:346px;top:0;height:27px;display:flex}
.toplinks a{display:flex;align-items:center;gap:5px;padding:0 12px;border-left:1px solid #333;font-size:6px;color:#ddd;text-decoration:none;height:27px}
.toplinks a:last-child{border-right:1px solid #333}

/* header */
.header{left:0;top:27px;width:667px;height:77px;background:#fff}
.brand{left:60px;top:15px;text-align:center;color:#111;font-weight:400;width:140px}
.brand .name{font-size:26px;line-height:30px;letter-spacing:.2px}
.brand .sub{font-size:14px;line-height:18px}
.search{left:320px;top:31px;width:180px;height:20px;background:#fff;border:1px solid #e2e2e2;box-shadow:0 0 4px rgba(0,0,0,.08);display:flex}
.search span{flex:1;font-size:6px;color:#bbb;font-style:italic;padding:6px 7px}
.search i{width:24px;border-left:1px solid #eee;display:flex;align-items:center;justify-content:center}
.cart{left:518px;top:33px;display:flex;gap:6px;align-items:center}
.cart strong{display:block;font-size:8px;font-weight:700;line-height:10px}
.cart span{display:block;font-size:5.5px;line-height:7px}

/* nav */
.nav{left:0;top:104px;width:667px;height:28px;background:var(--red)}
.nav ul{list-style:none;position:absolute;left:62px;top:0;display:flex;height:28px;border-left:1px solid #b11218}
.nav li{font-size:7.5px;color:#fff;display:flex;align-items:center;padding:0 11px;border-right:1px solid #b11218}
.nav li.active{background:var(--red-dark);padding:0 16px}

/* hero */
.hero{left:0;top:132px;width:667px;height:291px;background:var(--hero)}
.hero-photo{left:472px;top:0;width:195px;height:291px;background:linear-gradient(160deg,#6b4a3a 0%,#b9907a 45%,#3a2c28 100%)}
.hero-kicker{left:69px;top:78px;font-size:20px;font-weight:300;color:#fff}
.hero-title{left:69px;top:101px;font-size:24px;font-weight:600;color:#fff;letter-spacing:-.3px}
.hero-text{left:71px;top:137px;width:295px;font-size:7px;line-height:12.4px;color:#ddd}
.btn-red{background:var(--red);color:#fff;font-size:7.5px;display:flex;align-items:center;justify-content:center;text-transform:uppercase}
.hero-btn{left:71px;top:189px;width:81px;height:21px}

/* featured */
.section-title{left:62px;top:455px;font-size:20px;font-weight:400;color:#111}
.section-title em{font-style:normal;color:var(--red)}
.card{width:121px;height:219px;background:var(--card);border:1px solid #e4e4e4;text-align:center}
.card .photo{height:155px}
.card h3{font-size:7.5px;font-weight:400;color:#555;margin-top:8px;line-height:10px}
.card .price{font-size:8px;color:var(--red);margin-top:3px;line-height:10px}
.btn-dark{display:inline-flex;align-items:center;gap:4px;background:#1d1d1d;color:#fff;font-size:5.8px;height:16px;padding:0 9px;margin-top:5px}

.offer{left:466px;top:495px;width:140px;height:297px;background:linear-gradient(180deg,#6f5a66 0%,#a9939c 40%,#5d4d4f 75%,#2f2a2a 100%)}
.offer-box{left:474px;top:666px;width:124px;height:64px;background:rgba(20,20,20,.85);text-align:center;color:#fff;font-size:17px;font-weight:300;line-height:20px;padding-top:2px}
.offer-box .red{color:var(--red)}
.offer-btn{left:498px;top:738px;width:78px;height:22px;background:#fff;border:1px solid #ccc;font-size:7px;display:flex;align-items:center;justify-content:center}
.red-rule{height:3px;background:var(--red);width:140px;left:466px}

.newsletter{left:466px;top:818px;width:140px;height:136px;background:#fff;padding:0 9px}
.newsletter h3{font-size:14px;font-weight:400;color:#333;margin-top:15px;padding-bottom:2px;border-bottom:1px solid #e5e5e5;letter-spacing:.3px}
.newsletter p{font-size:6px;color:#555;line-height:7.5px;margin-top:6px}
.field{height:17px;border:1px solid #e5e5e5;font-size:6px;color:#aaa;padding:5px 6px;margin-top:6px}
.news-btn{left:540px;top:930px;width:55px;height:18px;font-size:6px}

/* footer */
.footer{left:0;top:992px;width:667px;height:208px;background:var(--footer);color:#ccc}
.f-head{font-size:12px;color:#e5e5e5;font-weight:400;letter-spacing:.3px}
.touch{left:64px;top:1039px}
.touch li{list-style:none;display:flex;gap:7px;font-size:7px;color:#bbb;height:19.5px;align-items:flex-start}
.touch svg{flex:none}
.links{left:218px;top:1035px;width:94px;list-style:none}
.links li{font-size:6px;color:#ddd;height:17px;border-bottom:1px solid #2c2c2c;display:flex;align-items:center;padding-left:7px;gap:5px}
.links li.on{background:var(--red);color:#fff}
.news{left:350px;width:120px;display:flex;gap:9px}
.news .thumb{width:34px;height:32px;border:2px solid #eee;background:linear-gradient(135deg,#8a9aa3,#3d4a52)}
.news b{display:block;font-size:6px;font-weight:400;color:#eee;margin-top:8px}
.news span{display:block;font-size:4.8px;color:#999;margin-top:2px}
.cform .in{position:absolute;left:488px;width:118px;background:var(--field);font-size:6px;color:#999;padding:4px 6px}
.submit{left:489px;top:1144px;width:47px;height:17px;background:#fff;color:#222;font-size:6px;font-weight:600;display:flex;align-items:center;justify-content:center}
.paycards{left:64px;top:1148px;display:flex;gap:4px}
.paycards i{display:block;width:18px;height:11px;background:#e9e9e9;border-radius:1px}
.paycards i:nth-child(2){background:#d9d9d9}
.bottom-links{left:62px;top:1180px;font-size:4.8px;color:#aaa;line-height:8px}
.social{left:484px;top:1176px;width:122px;height:24px;background:#232323;display:flex;justify-content:space-around;align-items:center;padding:0 6px}
.social i{display:block;width:8px;height:8px;border-radius:50%;background:#777}
</style>
</head>
<body>

<div class="abs topbar">
  <div class="abs support">
    <svg width="14" height="12" viewBox="0 0 14 12"><path d="M1 4c0-2 3-3 6-3s6 1 6 3v1h-3V4H4v1H1z" fill="#ccc"/><rect x="3" y="6" width="8" height="5" rx="1" fill="#ccc"/></svg>
    <div><strong>Support: +444(100) 5821</strong><span>Monday to Friday: 10:00am - 05:30pm</span></div>
  </div>
  <nav class="abs toplinks">
    <a><svg width="7" height="7" viewBox="0 0 8 8"><circle cx="4" cy="2.5" r="2" fill="#ccc"/><path d="M0 8c0-3 8-3 8 0z" fill="#ccc"/></svg>My Account</a>
    <a><svg width="7" height="7" viewBox="0 0 8 8"><path d="M4 7.5L.8 4.2A2 2 0 014 1.6a2 2 0 013.2 2.6z" fill="#ccc"/></svg>Wishlist</a>
    <a><svg width="9" height="7" viewBox="0 0 10 7"><rect x="0" y="1" width="6" height="4" fill="#ccc"/><path d="M6 2h2.5L10 4v1H6z" fill="#ccc"/><circle cx="2" cy="6" r="1" fill="#ccc"/><circle cx="8" cy="6" r="1" fill="#ccc"/></svg>Free Shipping</a>
    <a><svg width="6" height="7" viewBox="0 0 6 8"><path d="M1.5 3.5V2a1.5 1.5 0 013 0v1.5" stroke="#ccc" fill="none"/><rect x="0" y="3.5" width="6" height="4.5" fill="#ccc"/></svg>Log In</a>
  </nav>
</div>

<header class="abs header">
  <div class="abs brand"><div class="name">Lirvo Dune</div><div class="sub">Jewels</div></div>
  <div class="abs search"><span>Search here</span><i><svg width="7" height="7" viewBox="0 0 8 8"><circle cx="3.2" cy="3.2" r="2.4" stroke="#bbb" fill="none"/><path d="M5 5l2.5 2.5" stroke="#bbb"/></svg></i></div>
  <div class="abs cart">
    <svg width="18" height="15" viewBox="0 0 18 15"><path d="M1 5h16l-2 9H3z" fill="#222"/><path d="M5 5l3-4M13 5l-3-4" stroke="#222" stroke-width="1.3"/><path d="M6 7v5M9 7v5M12 7v5" stroke="#fff" stroke-width="1"/></svg>
    <div><strong>Shopping Cart:</strong><span>(0) Cart Stbtotal: $0.00</span></div>
  </div>
</header>

<nav class="abs nav">
  <ul>
    <li class="active">HOME</li><li>ONLINE SHOP</li><li>INFO &amp; FACTS</li><li>PARTNER</li><li>ABOUT ME</li><li>CONTACT</li>
  </ul>
</nav>

<section class="abs hero">
  <div class="abs hero-photo" role="img" aria-label="Model wearing drop earrings and a ring"></div>
  <div class="abs hero-kicker">Collection 2014</div>
  <h1 class="abs hero-title">Designer Jewelry</h1>
  <p class="abs hero-text">Lorem Ipsum is simply dummy text of the printing and typesetting industry. Lorem Ipsum has been the industry's standard dummy text ever since the 1500s, when an unknown printer took a galley of type and scrambled it to make a type. specimen book.</p>
  <div class="abs btn-red hero-btn">Shop Now</div>
</section>

<h2 class="abs section-title">Featured <em>Product</em></h2>

<div class="abs card" style="left:62px;top:495px"><div class="photo" role="img" aria-label="Model in white dress with pearl necklace" style="background:linear-gradient(160deg,#c9c3c0,#6e6563)"></div><h3>Jumper Dress In Baroque</h3><div class="price">$161.00</div><span class="btn-dark"><svg width="6" height="5" viewBox="0 0 6 5"><path d="M0 1.5h6L5 5H1z" fill="#fff"/></svg>SHOP NOW</span></div>
<div class="abs card" style="left:196px;top:495px"><div class="photo" role="img" aria-label="Model in lace dress with parasol" style="background:linear-gradient(160deg,#a7a0a3,#6c5e66)"></div><h3>Jumper Dress In Baroque</h3><div class="price">$161.00</div><span class="btn-dark"><svg width="6" height="5" viewBox="0 0 6 5"><path d="M0 1.5h6L5 5H1z" fill="#fff"/></svg>SHOP NOW</span></div>
<div class="abs card" style="left:330px;top:495px"><div class="photo" role="img" aria-label="Model in long gown on a balcony" style="background:linear-gradient(160deg,#4b5567,#a997a8)"></div><h3>Jumper Dress In Baroque</h3><div class="price">$161.00</div><span class="btn-dark"><svg width="6" height="5" viewBox="0 0 6 5"><path d="M0 1.5h6L5 5H1z" fill="#fff"/></svg>SHOP NOW</span></div>
<div class="abs card" style="left:62px;top:739px"><div class="photo" role="img" aria-label="Bridal gown on garden steps" style="background:linear-gradient(180deg,#6e6a55,#b8a78c)"></div><h3>Jumper Dress In Baroque</h3><div class="price">$161.00</div><span class="btn-dark"><svg width="6" height="5" viewBox="0 0 6 5"><path d="M0 1.5h6L5 5H1z" fill="#fff"/></svg>SHOP NOW</span></div>
<div class="abs card" style="left:196px;top:739px"><div class="photo" role="img" aria-label="Model wearing gold cuff and earrings" style="background:linear-gradient(160deg,#6a4c3c,#c9a58a)"></div><h3>Jumper Dress In Baroque</h3><div class="price">$161.00</div><span class="btn-dark"><svg width="6" height="5" viewBox="0 0 6 5"><path d="M0 1.5h6L5 5H1z" fill="#fff"/></svg>SHOP NOW</span></div>
<div class="abs card" style="left:330px;top:739px"><div class="photo" role="img" aria-label="Model wearing pearl bracelet" style="background:linear-gradient(160deg,#4e3a32,#b98f78)"></div><h3>Jumper Dress In Baroque</h3><div class="price">$161.00</div><span class="btn-dark"><svg width="6" height="5" viewBox="0 0 6 5"><path d="M0 1.5h6L5 5H1z" fill="#fff"/></svg>SHOP NOW</span></div>

<div class="abs offer" role="img" aria-label="Model in traditional dress by a window"></div>
<div class="abs offer-box">Special Offer<br>Save<br><span class="red">An Extra 40 %</span></div>
<div class="abs offer-btn">SHOP NOW</div>
<div class="abs red-rule" style="top:798px"></div>

<div class="abs newsletter">
  <h3>Our Newsletter</h3>
  <p>An example of how a subscription form could look like.</p>
  <div class="field" style="margin-top:10px">Name</div>
  <div class="field">E-mail Address</div>
</div>
<div class="abs btn-red news-btn">Shop Now</div>
<div class="abs red-rule" style="top:954px"></div>

<footer class="abs footer"></footer>
<div class="abs f-head" style="left:64px;top:1007px">Get in Touch</div>
<div class="abs f-head" style="left:217px;top:1007px">Useful Links</div>
<div class="abs f-head" style="left:350px;top:1007px">Latest News</div>
<div class="abs f-head" style="left:490px;top:1007px">Contact Us</div>

<ul class="abs touch">
  <li><svg width="8" height="8" viewBox="0 0 8 8"><path d="M1.5 0l1.5 2-1 1a5 5 0 003 3l1-1 2 1.5L7 8C3 8 0 5 0 1z" fill="#aaa"/></svg>(+1) 555 204 1187</li>
  <li><svg width="8" height="8" viewBox="0 0 8 8"><circle cx="4" cy="4" r="3.4" stroke="#aaa" fill="none"/><path d="M4 2v2h2" stroke="#aaa" fill="none"/></svg>Mon - Fri &nbsp;10:00am - 5:30 pm</li>
  <li><svg width="8" height="8" viewBox="0 0 8 8"><rect x="0" y="1.5" width="8" height="5" fill="#aaa"/><path d="M0 1.5l4 3 4-3" stroke="#1b1b1b" fill="none"/></svg>Mon - Fri &nbsp;10:00am - 5:30 pm</li>
  <li><svg width="8" height="8" viewBox="0 0 8 8"><circle cx="4" cy="4" r="3.6" fill="#aaa"/><path d="M.5 4h7M4 .5v7" stroke="#1b1b1b" stroke-width=".6"/></svg>Mon - Fri &nbsp;10:00am - 5:30 pm</li>
  <li><svg width="8" height="9" viewBox="0 0 8 9"><path d="M4 9L1 4.5a3 3 0 116 0z" fill="#aaa"/></svg><span style="line-height:8px">Mon - Fri &nbsp;10:00am - 5:30 pm<br>St Harlow TF - 450912</span></li>
</ul>
<div class="abs paycards" aria-label="Accepted payment cards"><i></i><i></i><i></i><i></i><i></i></div>

<ul class="abs links">
  <li>→ Neck lace</li><li class="on">→ Ring</li><li>→ Wrist gold watch</li><li>→ Wrist Diamond watch</li><li>→ Breslate</li><li>→ Wrist gold watch</li><li>→ Wrist Diamond watch</li>
</ul>

<div class="abs news" style="top:1034px"><div class="thumb" role="img" aria-label="News photo"></div><div><b>Just a Single Clean Post</b><span>february 03, 2013</span></div></div>
<div class="abs news" style="top:1076px"><div class="thumb" role="img" aria-label="News photo"></div><div><b>Just a Single Clean Post</b><span>february 10, 2013</span></div></div>
<div class="abs news" style="top:1118px"><div class="thumb" role="img" aria-label="News photo"></div><div><b>Just a Single Clean Post</b><span>february 15, 2013</span></div></div>

<div class="cform">
  <div class="in" style="top:1034px;height:17px">Name*</div>
  <div class="in" style="top:1056px;height:17px">Email Address*</div>
  <div class="in" style="top:1078px;height:60px">Message*</div>
</div>
<div class="abs submit">SUBMIT</div>

<div class="abs bottom-links">Home &nbsp;|&nbsp; Products &nbsp;|&nbsp; About Lirvo &nbsp;|&nbsp; Special Offers &nbsp;|&nbsp; Contact Us<br>© Copyrights 2013 All rights Reserved</div>
<div class="abs social" aria-label="Social links"><i></i><i></i><i></i><i></i><i></i></div>

</body>
</html>
```